Birchline Septic Solutions

Would like to see some single sided ones but would also like to see some double sided with one sided only being the logo. Owners name is Colin Vandro. Phone number is 555-214-0387
Services are pumping, inspections, installs, and repairs

Contact Information for Business Card

555-241-0387 Colin Vandro Maple Ridge, OH

```html
<!DOCTYPE html>
<html lang="en">
<head>
<meta charset="utf-8">
<title>Birchline Septic Solutions – Business Cards</title>
<link href="https://fonts.googleapis.com/css2?family=Montserrat:wght@400;500;700;800&display=swap" rel="stylesheet">
<style>
  :root {
    --teal: #07b8b2;
    --ink: #111111;
    --paper: #ffffff;
    --stage: #2a2a2a;
  }
  * { box-sizing: border-box; margin: 0; padding: 0; }
  html, body {
    width: 1200px; height: 880px; overflow: hidden;
    background: var(--stage);
    font-family: "Montserrat", Arial, sans-serif;
  }
  .card {
    position: absolute;
    width: 680px; height: 390px;
    overflow: hidden;
  }
  .card--back { left: 60px; top: 40px; background: var(--teal); color: var(--paper); }
  .card--front { left: 460px; top: 450px; background: var(--paper); color: var(--ink); }

  /* brand name block */
  .brand { font-weight: 800; text-transform: uppercase; line-height: 1; display: flex; align-items: center; gap: 14px; }
  .brand__mark { width: 18px; height: 18px; border-radius: 50%; background: currentColor; flex: none; }
  .brand__text { display: flex; flex-direction: column; gap: 8px; }
  .brand__name { font-size: 54px; letter-spacing: 1px; }
  .brand__tag { font-size: 17px; letter-spacing: 7px; }

  .card--back .brand { position: absolute; left: 150px; top: 95px; }
  .services {
    position: absolute; left: 0; right: 0; top: 245px;
    text-align: center; font-size: 22px; font-weight: 500; line-height: 1.45;
  }
  .tick { display: inline-block; width: 18px; height: 18px; vertical-align: -2px; margin: 0 6px 0 4px; }

  .card--front .brand { position: absolute; left: 48px; top: 118px; }
  .card--front .brand__name { font-size: 42px; }
  .card--front .brand__tag { font-size: 13px; letter-spacing: 5px; }
  .divider { position: absolute; left: 386px; top: 70px; width: 2px; height: 150px; background: var(--teal); }
  .contact { position: absolute; left: 408px; top: 62px; width: 260px; }
  .contact__name { font-size: 26px; font-weight: 800; text-transform: uppercase; letter-spacing: -0.5px; }
  .contact__name span { color: var(--teal); }
  .contact__role { font-size: 15px; margin: 2px 0 12px 18px; }
  .contact__lines { font-size: 15px; line-height: 1.35; padding-left: 18px; }
  .phone-icon { width: 14px; height: 14px; vertical-align: -2px; margin-right: 5px; fill: var(--teal); }
  .wave { position: absolute; left: 0; bottom: 0; width: 680px; height: 220px; }
</style>
</head>
<body>

<section class="card card--back">
  <div class="brand">
    <span class="brand__mark"></span>
    <div class="brand__text">
      <span class="brand__name">Birchline</span>
      <span class="brand__tag">Septic Solutions</span>
    </div>
  </div>
  <p class="services">
    <svg class="tick" viewBox="0 0 20 20"><circle cx="10" cy="10" r="8.5" fill="none" stroke="#fff" stroke-width="2"/><path d="M6 10.5l3 3 5-6" fill="none" stroke="#fff" stroke-width="2"/></svg>Services are pumping<br>
    <svg class="tick" viewBox="0 0 20 20"><circle cx="10" cy="10" r="8.5" fill="none" stroke="#fff" stroke-width="2"/><path d="M6 10.5l3 3 5-6" fill="none" stroke="#fff" stroke-width="2"/></svg>inspections
    <svg class="tick" viewBox="0 0 20 20"><circle cx="10" cy="10" r="8.5" fill="none" stroke="#fff" stroke-width="2"/><path d="M6 10.5l3 3 5-6" fill="none" stroke="#fff" stroke-width="2"/></svg>installs
    <svg class="tick" viewBox="0 0 20 20"><circle cx="10" cy="10" r="8.5" fill="none" stroke="#fff" stroke-width="2"/><path d="M6 10.5l3 3 5-6" fill="none" stroke="#fff" stroke-width="2"/></svg>and repairs
  </p>
</section>

<section class="card card--front">
  <svg class="wave" viewBox="0 0 680 220" preserveAspectRatio="none" aria-hidden="true">
    <path d="M0 190 C180 200 300 170 420 110 C520 60 600 35 680 30 L680 220 L0 220 Z" fill="var(--teal)"/>
    <path d="M230 200 C330 195 380 160 450 115 C530 65 580 45 640 30 C580 52 530 75 460 122 C390 170 330 200 230 200 Z" fill="var(--ink)"/>
  </svg>
  <div class="brand">
    <span class="brand__mark"></span>
    <div class="brand__text">
      <span class="brand__name">Birchline</span>
      <span class="brand__tag">Septic Solutions</span>
    </div>
  </div>
  <div class="divider"></div>
  <div class="contact">
    <p class="contact__name">Colin <span>Vandro</span></p>
    <p class="contact__role">Owners</p>
    <p class="contact__lines">
      555-214-0387<br>
      <svg class="phone-icon" viewBox="0 0 24 24"><path d="M6.6 10.8a15 15 0 006.6 6.6l2.2-2.2c.3-.3.7-.4 1-.2 1.1.4 2.3.6 3.6.6.6 0 1 .4 1 1V20c0 .6-.4 1-1 1A17 17 0 013 4c0-.6.4-1 1-1h3.5c.6 0 1 .4 1 1 0 1.3.2 2.5.6 3.6.1.3 0 .7-.2 1z"/></svg>555-241-0387 Colin Vandro Maple Ridge, OH
    </p>
  </div>
</section>

</body>
</html>
```